Small Business Broker Business Card Design

A business card design for a small business brokerage, which is a financial service, not unlike real estate brokerage, but for small businesses such as laundromats, pizza shops, restaurants, cleaners etc. The designs should all be simple, more conservative in nature, using the colors and font of the logo. Again, think real estate Brokerage as a business context
Contact Information for Business Card
Name: Glen R. Harlow. Title: Small Business Advisor. Email: g.harlow@bayfieldcapitalworks.example. Mobile: (555) 274-3918. Office: (555) 806-2147. www.bayfieldcapitalworks.example

```html
<!DOCTYPE html>
<html lang="en">
<head>
<meta charset="utf-8">
<title>Bayfield Capital Works — Business Card</title>
<link rel="stylesheet" href="https://fonts.googleapis.com/css2?family=Montserrat:wght@500;600;700&family=Arimo:wght@400&display=swap">
<style>
  :root {
    --navy: #1c3a6b;
    --green: #8cc63f;
    --white: #ffffff;
    --ink: #2b2b2b;
    --stage: #e4e4e6;
  }
  * { box-sizing: border-box; margin: 0; padding: 0; }
  html, body { width: 1200px; height: 900px; overflow: hidden; }
  body {
    background: var(--stage);
    font-family: "Arimo", Arial, sans-serif;
    position: relative;
  }
  .card {
    position: absolute;
    left: 250px;
    width: 700px;
    height: 400px;
    border-radius: 24px;
    overflow: hidden;
    box-shadow: 0 6px 18px rgba(0,0,0,0.18);
  }
  .card--front { top: 40px; background: var(--navy); }
  .card--back { top: 470px; background: var(--white); }

  .brand { font-family: "Montserrat", Arial, sans-serif; }
  .brand__row { display: flex; align-items: center; gap: 14px; }
  .brand__mark { width: 22px; height: 22px; background: var(--green); flex: none; }
  .brand__name {
    font-weight: 700;
    text-transform: uppercase;
    letter-spacing: 0.04em;
    white-space: nowrap;
  }
  .brand__tagline {
    color: var(--green);
    font-weight: 600;
    text-transform: uppercase;
    letter-spacing: 0.12em;
    white-space: nowrap;
  }

  .card--front .brand {
    position: absolute;
    left: 0; right: 0; top: 160px;
    display: flex; flex-direction: column; align-items: center; gap: 10px;
  }
  .card--front .brand__name { color: var(--white); font-size: 32px; }
  .card--front .brand__tagline { font-size: 14px; }

  .card--back .brand {
    position: absolute; left: 60px; top: 52px;
    display: flex; flex-direction: column; gap: 6px;
  }
  .card--back .brand__mark { width: 18px; height: 18px; background: var(--navy); }
  .card--back .brand__name { color: var(--navy); font-size: 24px; }
  .card--back .brand__tagline { font-size: 11px; padding-left: 32px; }

  .person { position: absolute; left: 92px; top: 150px; }
  .person__name {
    font-family: "Montserrat", Arial, sans-serif;
    font-weight: 700;
    font-size: 34px;
    color: var(--navy);
    letter-spacing: 0.02em;
    text-transform: uppercase;
  }
  .person__surname { color: var(--green); }
  .person__title { font-size: 19px; color: var(--ink); margin-top: 4px; }

  .contact {
    position: absolute; left: 92px; top: 258px;
    list-style: none;
    display: flex; flex-direction: column; gap: 7px;
  }
  .contact__item {
    display: flex; align-items: center; gap: 14px;
    font-size: 17px; color: var(--ink);
  }
  .contact__icon { width: 16px; height: 16px; flex: none; fill: var(--green); }
</style>
</head>
<body>

<section class="card card--front" aria-label="Card front">
  <div class="brand">
    <div class="brand__row">
      <span class="brand__mark"></span>
      <span class="brand__name">Bayfield Capital Works, Inc</span>
    </div>
    <span class="brand__tagline">Confidently buy or sell a local business today</span>
  </div>
</section>

<section class="card card--back" aria-label="Card back">
  <div class="brand">
    <div class="brand__row">
      <span class="brand__mark"></span>
      <span class="brand__name">Bayfield Capital Works, Inc</span>
    </div>
    <span class="brand__tagline">Confidently buy or sell a local business today</span>
  </div>

  <div class="person">
    <h1 class="person__name">Glen R. <span class="person__surname">Harlow</span></h1>
    <p class="person__title">Small Business Advisor</p>
  </div>

  <ul class="contact">
    <li class="contact__item">
      <svg class="contact__icon" viewBox="0 0 16 16" aria-hidden="true"><path d="M1 5c0-2 3-3 7-3s7 1 7 3v1.5h-3.5V5h-7v1.5H1zM3 8l2-1.5h6L13 8v6H3zm5 1.2a2 2 0 1 0 0 4 2 2 0 0 0 0-4z"/></svg>
      <span>(555) 806-2147</span>
    </li>
    <li class="contact__item">
      <svg class="contact__icon" viewBox="0 0 16 16" aria-hidden="true"><path d="M4 1h8v14H4zm1.5 1.5v9h5v-9zM7 12.5v1h2v-1z"/></svg>
      <span>(555) 274-3918</span>
    </li>
    <li class="contact__item">
      <svg class="contact__icon" viewBox="0 0 16 16" aria-hidden="true"><path d="M1 4h14v9H1zm1.5 1.2v.4L8 9.3l5.5-3.7v-.4zM2.5 7.3v4.2h11V7.3L8 11z"/></svg>
      <span>g.harlow@bayfieldcapitalworks.example</span>
    </li>
    <li class="contact__item">
      <svg class="contact__icon" viewBox="0 0 16 16" aria-hidden="true"><path d="M8 1a7 7 0 1 0 0 14A7 7 0 0 0 8 1zm0 1.5c.9 0 1.9 1.9 2.2 4.7H5.8C6.1 4.4 7.1 2.5 8 2.5zM5.8 8.8h4.4c-.3 2.8-1.3 4.7-2.2 4.7s-1.9-1.9-2.2-4.7zM2.6 7.2a5.5 5.5 0 0 1 2.6-4c-.5 1-.8 2.4-.9 4zm0 1.6h1.7c.1 1.6.4 3 .9 4a5.5 5.5 0 0 1-2.6-4zm10.8 0a5.5 5.5 0 0 1-2.6 4c.5-1 .8-2.4.9-4zm0-1.6h-1.7c-.1-1.6-.4-3-.9-4a5.5 5.5 0 0 1 2.6 4z"/></svg>
      <span>www.bayfieldcapitalworks.example</span>
    </li>
  </ul>
</section>

</body>
</html>
```